I will ask the design of the business card

We are looking for business card design of the new company "R DOVE PAYGRID WORKS LLC." Based in Azerbaijan.
In case
We are working on Azerbaijan to set up the first exchange of crypto currencies.

The key currency used in exchanges is called "PLUME".
In case
We are doing project to make crypto currency infrastructure.

We provide state-of-the-art technology to the world.

```html
<!DOCTYPE html>
<html lang="en">
<head>
<meta charset="utf-8">
<title>R Dove Paygrid Works LLC — Business Card</title>
<link rel="stylesheet" href="https://fonts.googleapis.com/css2?family=Jost:wght@400&family=Oswald:wght@600&family=Work+Sans:wght@400&display=swap">
<style>
  :root {
    --bg: #1c1c1e;
    --card: #121213;
    --card-edge: #0b0b0c;
    --gloss: #2a2a2c;
    --ink-light: #d9d9dc;
    --ink-mid: #8a8a8e;
    --ink-dark: #3a3a3d;
    --rule: #3d3d40;
  }
  * { margin: 0; padding: 0; box-sizing: border-box; }
  html, body { width: 1200px; height: 900px; overflow: hidden; background: var(--bg); }
  .canvas {
    position: relative; width: 1200px; height: 900px;
    background: radial-gradient(ellipse at 50% 45%, #252527 0%, var(--bg) 70%);
  }
  .card {
    position: absolute; left: 290px; width: 620px; height: 354px;
    background: linear-gradient(135deg, var(--card) 0%, #1a1a1c 60%, var(--card) 100%);
    box-shadow: 0 14px 30px rgba(0,0,0,.55), 0 0 0 1px var(--card-edge);
  }
  .card--front { top: 76px; }
  .card--back { top: 470px; }

  .brand {
    position: absolute; left: 0; right: 0; top: 152px;
    display: flex; align-items: center; justify-content: center; gap: 14px;
  }
  .brand__dot { width: 30px; height: 30px; border-radius: 50%; background: var(--ink-dark); }
  .brand__name {
    font-family: "Jost", sans-serif; font-weight: 400; font-size: 31px;
    letter-spacing: 1px; color: var(--ink-light);
  }

  .person { position: absolute; left: 60px; top: 118px; text-align: right; width: 220px; }
  .person__name {
    font-family: "Oswald", sans-serif; font-weight: 600; font-size: 34px;
    letter-spacing: 1px; color: var(--ink-dark); line-height: 1;
  }
  .person__role {
    font-family: "Work Sans", sans-serif; font-size: 15px; color: var(--ink-dark);
    margin-top: 4px; letter-spacing: .5px;
  }
  .divider { position: absolute; left: 300px; top: 114px; width: 1px; height: 64px; background: var(--rule); }

  .contacts { position: absolute; left: 318px; top: 118px; list-style: none; }
  .contacts li {
    display: flex; align-items: center; gap: 10px; height: 20px;
    font-family: "Work Sans", sans-serif; font-size: 16px; color: var(--ink-light);
    letter-spacing: .6px;
  }
  .contacts svg { width: 12px; height: 12px; fill: none; stroke: var(--ink-mid); stroke-width: 1.6; }

  .address {
    position: absolute; left: 60px; top: 282px;
    font-family: "Work Sans", sans-serif; font-size: 17px; letter-spacing: .6px;
    color: var(--ink-mid);
  }
</style>
</head>
<body>
<main class="canvas">
  <section class="card card--front" aria-label="Card front">
    <div class="brand">
      <span class="brand__dot"></span>
      <span class="brand__name">R DOVE PAYGRID WORKS LLC.</span>
    </div>
  </section>

  <section class="card card--back" aria-label="Card back">
    <div class="person">
      <div class="person__name">DANIEL HART</div>
      <div class="person__role">Director</div>
    </div>
    <span class="divider"></span>
    <ul class="contacts">
      <li>
        <svg viewBox="0 0 12 12"><path d="M2.5 1.5l2 .3.6 2.4-1.2.9a6 6 0 0 0 3 3l.9-1.2 2.4.6.3 2c-4.5.8-8.8-3.5-8-8z"/></svg>
        615-555-0142
      </li>
      <li>
        <svg viewBox="0 0 12 12"><rect x="1" y="2.5" width="10" height="7"/><path d="M1 2.5l5 4 5-4"/></svg>
        support@plume.technology
      </li>
      <li>
        <svg viewBox="0 0 12 12"><circle cx="6" cy="6" r="5"/><ellipse cx="6" cy="6" rx="2.2" ry="5"/><path d="M1 6h10"/></svg>
        www.guild.plume.technology
      </li>
    </ul>
    <p class="address">AZ1010 , 8/22 Nizami str. Baku city, Azerbaijan</p>
  </section>
</main>
</body>
</html>
```